Website Design for Chef Wen Chinese Restaurant

Chef Wen is a new Chinese Restaurant. It offers exceptional dining experience with authentic and dynamic dishes created with quality ingredients.

A vivid website theme is required to promote this new restaurant online. Logo, menu, wine list and a few other files are attached for help with designing.

A very rough demo website has been setup and can be accessed via http://www.chefwen.com.au. It is for telling designers what content is shown up on each page (except for homepage). By reading the about us page, designers can get some more info of Chef Wen. However, the layout, theme color, font, etc are not set in stone. Visitors should be able to feel Chef Wen restaurant's authentic Chinese cuisine and high hygiene standard. Home page of the website could be The "Our website is coming soon" description is shown on demo site but do not required to be presented on new design.

Some main pages design should be included: Home (landing page), About us, Menu (Dishes), Winelist, Gallery, Contact us. No HTML and coding required. The output should be well layered psd or png files with acceptable resolution for web use.

A few other website can be referred to are:

http://larkspurasian.com.au/
http://www.river-lamp.com/
http://tamworthy.com.au/
http://harbelrestaurant.com.au/
http://www.quillerestaurant.com.au/
http://www.thekiln.com.au/

Industry/Entity Type

Restaurant

Requirements
Nice to have
• I expect designs of at least these webpages: homepage, menu page and contact us page. If you can provide "about us" page as well, it will probably help you win the competition. well layered psd or png file is my preference.
Should not have
• You don't have to make html/cs/js or any coding. All I need is just art design

```html
<!DOCTYPE html>
<html lang="en">
<head>
<meta charset="utf-8">
<title>Chef Wen Chinese Restaurant</title>
<link href="https://fonts.googleapis.com/css2?family=Ubuntu:wght@400;500;700&family=Arimo:wght@400;700&display=swap" rel="stylesheet">
<style>
:root{
  --red:#d7100f;
  --red-dark:#c20c0c;
  --red-soft:#ee6a6a;
  --cream:#fffdf0;
  --ink:#222222;
  --grey:#666666;
  --line:#9a9a8a;
  --white:#ffffff;
}
*{margin:0;padding:0;box-sizing:border-box}
html,body{width:809px;height:1200px;overflow:hidden}
body{position:relative;background:var(--cream);font-family:Arimo,Arial,sans-serif;color:var(--ink)}
.abs{position:absolute}
.top-rule{left:0;top:0;width:809px;height:2px;background:var(--red)}
.brand{left:96px;top:30px;display:flex;align-items:center;gap:6px}
.brand-mark{width:14px;height:14px;background:var(--red)}
.brand-name{font-family:Ubuntu,sans-serif;font-size:15px;font-weight:700;color:var(--ink)}
.nav{top:34px;display:flex;align-items:center;font-family:Ubuntu,sans-serif;font-size:9.5px;color:var(--ink)}
.nav a{color:inherit;text-decoration:none;padding:5px 9px;margin-right:6px}
.nav a.active{background:var(--red);color:var(--white);border-radius:2px}
.hero{left:0;top:86px;width:809px;height:395px;background:radial-gradient(ellipse at 60% 45%,#f6e07a 0%,#f1cf6a 30%,#c9735a 60%,#8a4a36 100%)}
.hero-arrow{top:268px;width:14px;height:26px}
.thumbs{left:95px;top:426px;width:619px;height:92px;background:var(--white);box-shadow:0 8px 10px -6px rgba(0,0,0,.25)}
.thumb{top:10px;width:138px;height:72px}
.divider{left:97px;width:612px;height:8px}
.divider::before,.divider::after{content:"";position:absolute;top:3px;border-top:1px dotted var(--line);width:292px}
.divider::before{left:0}.divider::after{right:0}
.divider i{position:absolute;left:302px;top:0;width:8px;height:8px;border-radius:50%;background:#555}
h2{position:absolute;font-family:Ubuntu,sans-serif;font-weight:400;font-size:17px;color:var(--ink)}
h2 span{color:var(--red)}
.welcome-pic{left:97px;top:604px;width:98px;height:98px;border-radius:50%;border:3px solid var(--white);box-shadow:0 1px 4px rgba(0,0,0,.25);background:radial-gradient(circle,#c8703e 0%,#b05a30 45%,#f2ece4 70%)}
.intro{left:210px;top:602px;width:208px;font-size:7.6px;line-height:14px;color:var(--grey);text-align:justify}
.btn{height:17px;padding:0 9px;background:var(--red);color:var(--white);font-size:8px;line-height:17px;border-radius:2px}
.menu-list{left:463px;top:601px;width:206px;list-style:none;font-size:7.4px;color:var(--grey)}
.menu-list li{display:flex;justify-content:space-between;line-height:14.5px}
.menu-list li::before{content:"";width:2px;height:2px;background:var(--red);margin:6px 6px 0 0;flex:none}
.menu-list li span:first-of-type{flex:1}
.pager{top:744px;width:19px;height:17px;border-radius:2px;display:flex;align-items:center;justify-content:center}
.card{top:791px;width:138px}
.card-pic{height:88px;border:3px solid var(--white);box-shadow:0 0 3px rgba(0,0,0,.2)}
.card-title{margin-top:15px;font-size:7.6px;color:var(--ink)}
.card-sub{margin-top:4px;font-size:7.4px;color:#888}
.footer{left:0;top:950px;width:809px;height:206px;background:var(--red);color:var(--white);font-family:Ubuntu,sans-serif}
.footer h3{position:absolute;top:17px;font-size:12.5px;font-weight:500}
.col-sep{top:20px;width:1px;height:155px;background:rgba(0,0,0,.12)}
.contact{left:94px;top:52px;font-size:7.6px;line-height:18px}
.contact div{display:flex;align-items:center;gap:6px}
.contact svg{width:10px;height:10px;flex:none}
.social{left:95px;top:148px;display:flex;gap:9px}
.social i{width:20px;height:20px;display:block}
.hours{left:291px;top:52px;font-size:7.6px;line-height:18px}
.hours b{font-size:9px;font-weight:500;display:block}
.map{left:490px;top:53px;width:222px;height:121px;background:linear-gradient(135deg,#e9e5dc,#dcd8cc);border:1px solid #ccc}
.bottom{left:0;top:1156px;width:809px;height:44px;background:var(--red-dark);color:var(--white);font-family:Ubuntu,sans-serif;font-size:7.6px;text-align:center;line-height:44px}
</style>
</head>
<body>
<div class="abs top-rule"></div>

<div class="abs brand"><span class="brand-mark"></span><span class="brand-name">Chef Wen</span></div>

<nav class="abs nav" style="left:277px">
  <a class="active">HOME</a><a>ABOUT US</a><a>MENU</a><a>WINE LIST</a><a>GALLERY</a><a>CONTACT US</a><a>LOTUS COURT</a>
</nav>

<div class="abs hero" role="img" aria-label="Breakfast plate with scrambled eggs and crispy bacon"></div>
<svg class="abs hero-arrow" style="left:24px" viewBox="0 0 14 26"><path d="M12 1 2 13l10 12" fill="none" stroke="#fff" stroke-opacity=".7" stroke-width="2"/></svg>
<svg class="abs hero-arrow" style="left:772px" viewBox="0 0 14 26"><path d="M2 1l10 12L2 25" fill="none" stroke="#fff" stroke-opacity=".7" stroke-width="2"/></svg>

<div class="abs thumbs">
  <div class="abs thumb" style="left:10px;background:linear-gradient(135deg,#e9c97a,#c46a52)" role="img" aria-label="Eggs and bacon"></div>
  <div class="abs thumb" style="left:163px;background:linear-gradient(135deg,#b9c79a,#c9803c)" role="img" aria-label="French toast with ice cream"></div>
  <div class="abs thumb" style="left:315px;background:linear-gradient(135deg,#e5a34e,#c9a277)" role="img" aria-label="Pancakes with fruit"></div>
  <div class="abs thumb" style="left:468px;background:linear-gradient(135deg,#9bbd5a,#6a3a28)" role="img" aria-label="Steak with salad"></div>
</div>

<div class="abs divider" style="top:544px"><i></i></div>

<h2 style="left:97px;top:570px">WELCOME TO <span>CHEFWEN</span></h2>
<div class="abs welcome-pic" role="img" aria-label="Steamed sponge cake with a flower"></div>
<p class="abs intro">Chef Wen is named after its' executive chef, Mr. Wen. Chef Wen has been in his career for nearly two decades before he moved to Australia nine years ago. He settled in Adelaide then started his first restaurant, Lotus Court in Norwood. Lotus Court has been</p>
<div class="abs btn" style="left:211px;top:683px">MORE</div>

<h2 style="left:461px;top:570px">OUR <span>MENU</span></h2>
<ul class="abs menu-list">
  <li><span>Spring Rolls (3 per serve)</span><span>6.8</span></li>
  <li><span>Steamed or Deep Fried Dim Sim (3 per serve)</span><span>6.8</span></li>
  <li><span>Satay Beef Skewers (3)</span><span>7.8</span></li>
  <li><span>Satay Chicken Skewers (3)</span><span>7.8</span></li>
  <li><span>Deep Fried mix Vegetable</span><span>6.8</span></li>
</ul>
<div class="abs btn" style="left:463px;top:683px">MORE</div>

<div class="abs divider" style="top:725px"><i></i></div>

<h2 style="left:97px;top:751px">BEST <span>CHOICE</span></h2>
<div class="abs pager" style="left:662px;background:var(--red-soft)"><svg width="6" height="9" viewBox="0 0 6 9"><path d="M5 1 1 4.5 5 8" fill="none" stroke="#fff" stroke-width="1.4"/></svg></div>
<div class="abs pager" style="left:683px;background:var(--red)"><svg width="6" height="9" viewBox="0 0 6 9"><path d="M1 1l4 3.5L1 8" fill="none" stroke="#fff" stroke-width="1.4"/></svg></div>

<div class="abs card" style="left:108px"><div class="card-pic" style="background:linear-gradient(135deg,#d9b77a,#b88a48)" role="img" aria-label="Dumplings in a bamboo steamer"></div><div class="card-title">LOREM IPSUM DOAMET CONSECTET</div><div class="card-sub">Dorem ipsum dolor amet consectetur</div></div>
<div class="abs card" style="left:260px"><div class="card-pic" style="background:linear-gradient(135deg,#f2efe6,#d9d2bf)" role="img" aria-label="Boiled dumplings on a plate"></div><div class="card-title">LOREM IPSUM DOAMET CONSECTET</div><div class="card-sub">Dorem ipsum dolor amet consectetur</div></div>
<div class="abs card" style="left:411px"><div class="card-pic" style="background:linear-gradient(135deg,#f4f1ea,#d99a4e)" role="img" aria-label="Fried dough sticks on a leaf"></div><div class="card-title">LOREM IPSUM DOAMET CONSECTET</div><div class="card-sub">Dorem ipsum dolor amet consectetur</div></div>
<div class="abs card" style="left:563px"><div class="card-pic" style="background:linear-gradient(135deg,#e9a75a,#f3ede2)" role="img" aria-label="Pan fried radish cake"></div><div class="card-title">LOREM IPSUM DOAMET CONSECTET</div><div class="card-sub">Dorem ipsum dolor amet consectetur</div></div>

<footer class="abs footer">
  <h3 style="left:94px">CONTACT DETAILS</h3>
  <h3 style="left:291px">TRADING HOURS</h3>
  <h3 style="left:485px">LOCATION</h3>
  <div class="abs col-sep" style="left:253px"></div>
  <div class="abs col-sep" style="left:450px"></div>

  <div class="abs contact">
    <div><svg viewBox="0 0 10 10"><path d="M1 3c0-1 1-2 4-2s4 1 4 2v1H7V3H3v1H1zM2 5h6l1 4H1z" fill="#fff"/></svg>Phone: 08 8000 4172</div>
    <div><svg viewBox="0 0 10 10"><rect x="1" y="2.5" width="8" height="5.5" fill="#fff"/><path d="M1 2.5l4 3 4-3" fill="none" stroke="#d7100f" stroke-width=".8"/></svg>Email: info@chefwen.com.au/</div>
    <div><svg viewBox="0 0 10 10"><path d="M5 9.5S1.5 5.5 1.5 3.6a3.5 3.5 0 0 1 7 0C8.5 5.5 5 9.5 5 9.5z" fill="#fff"/><circle cx="5" cy="3.6" r="1.3" fill="#d7100f"/></svg>7/41 Kestrel Road</div>
    <div style="padding-left:16px">Elm Vale,</div>
    <div style="padding-left:16px">SA, 5070</div>
  </div>
  <div class="abs social">
    <i style="background:#2f5aa8"></i><i style="background:#1a9be0"></i><i style="background:#a40f0f"></i><i style="background:#f29a2e"></i><i style="background:#1679b4"></i>
  </div>

  <div class="abs hours">
    <b>WE ARE OPEN 7 DAYS</b>
    <b>Lunch</b>
    <div>Monday to Friday 11:30am - 2:30pm</div>
    <div>Saturday to Sunday 11:00am - 3:00pm</div>
    <b>Dinner</b>
    <div>Monday to Sunday 6:00pm Until Late</div>
  </div>

  <div class="abs map" role="img" aria-label="Street map showing the restaurant location"></div>
</footer>

<div class="abs bottom">© 2014 Copyright by chefwen | All rights reserved</div>
</body>
</html>
```